We would like to obtain a sales orientated brochure to promote our two models of thermal imaging cameras as a response to the current Covid 19 health issues. I have provided the text, photos and detailed product specifications , in addition to a sample competitors brochure.
BROCHURE Details : 2 sided - front side to show product, its applications in business, school, hospitals, with text details - Back page to show specifications chart and contact information for Korvel Display Group. (Melbourne -Sydney-Perth-Brisbane - 1300 618 475
Brochure should be "eye-catching" and reflect the product as a high quality, must-have technology device for todays world.

```html
<!DOCTYPE html>
<html lang="en">
<head>
<meta charset="utf-8">
<title>Thermal Scanning Camera Brochure – Korvel Display Group</title>
<link href="https://fonts.googleapis.com/css2?family=Bebas+Neue&family=Montserrat:wght@400;500;600;700;800;900&display=swap" rel="stylesheet">
<style>
  :root{
    --navy:#133d91;
    --navy-deep:#0f3384;
    --accent:#1f4fa8;
    --sky:#4f8fe0;
    --sky-soft:#7fb0ec;
    --ink:#2b2b2b;
    --line:#cfd6e2;
    --backdrop:#b4b4b4;
    --paper:#ffffff;
  }
  *{box-sizing:border-box;margin:0;padding:0}
  html,body{width:800px;height:1200px;overflow:hidden}
  body{background:var(--backdrop);font-family:"Montserrat",sans-serif;color:var(--ink);position:relative}

  .sheet{position:absolute;top:331px;width:648px;height:917px;background:var(--paper);
    transform:scale(0.586);transform-origin:0 0;overflow:hidden}
  .sheet--front{left:13px}
  .sheet--back{left:407px}
  .sheet > *{position:absolute}
  .backdrop-art{left:0;top:0}

  /* front header */
  .product-photo{left:22px;top:26px;width:300px;height:325px;border-radius:10px;
    background:radial-gradient(ellipse at 40% 45%,#e9ecf1 0%,#9aa3b1 45%,#2a2f3a 100%)}
  .title{left:325px;top:40px;color:#fff;line-height:1}
  .title__thermal{font-family:"Bebas Neue",sans-serif;font-size:48px;letter-spacing:1px;display:block}
  .title__scanning{font-family:"Bebas Neue",sans-serif;font-size:70px;letter-spacing:1px;display:block;margin-top:-2px}
  .title__sub{font-weight:800;font-size:19px;letter-spacing:.5px;display:block;margin-top:-4px}
  .title__camera{font-weight:900;font-size:66px;letter-spacing:1px;display:block;margin-top:2px}

  .copy{width:270px;font-size:11px;line-height:12.9px;text-align:justify}
  .copy p{margin-bottom:12px}
  .copy h3{color:var(--accent);font-size:12px;font-weight:700;line-height:14px;margin:14px 0 12px;text-align:left}
  .copy--left{left:33px;top:372px}
  .copy--right{left:348px;top:372px}
  .copy--right h3{margin-top:0}

  .model-card{left:347px;width:272px;height:124px;border:1.5px solid var(--line);border-radius:6px;background:#fff}
  .model-card--desk{top:549px}
  .model-card--floor{top:684px}
  .model-card__name{position:absolute;left:13px;top:50%;transform:translateY(-50%);
    color:var(--sky);font-weight:700;font-size:12.5px;line-height:16px;letter-spacing:.4px;width:148px}
  .model-card__photo{position:absolute;right:8px;top:8px;width:98px;height:106px;border-radius:6px;
    background:linear-gradient(160deg,#f3f5f8 0%,#b7bec9 60%,#3a3f49 100%)}

  /* footer */
  .brand{left:34px;top:832px;display:flex;align-items:center;gap:10px;
    font-size:19px;font-weight:500;color:#111;white-space:nowrap}
  .brand__mark{width:16px;height:16px;background:var(--navy)}
  .contact{left:363px;top:832px;color:#fff;white-space:nowrap}
  .contact__phone{display:flex;align-items:center;gap:12px;font-size:22px;font-weight:700;letter-spacing:.5px}
  .contact__note{font-size:10.5px;margin:1px 0 0 32px}
  .contact__web{display:flex;align-items:center;gap:12px;font-size:11px;margin-top:7px}
  .contact--short .contact__web{margin-top:6px}

  /* back page */
  .spec-title{left:0;top:70px;width:648px;text-align:center;color:#fff;
    font-family:"Bebas Neue",sans-serif;font-size:54px;letter-spacing:1px}
  .spec-col{width:290px;font-size:8.6px;line-height:10.2px}
  .spec-col--left{left:34px;top:186px}
  .spec-col--right{left:347px;top:190px}
  .spec-col h4{color:var(--accent);font-size:11.5px;font-weight:600;letter-spacing:.4px;margin:14px 0 6px}
  .spec-col h4:first-child{margin-top:0}
  .spec-row{display:grid;grid-template-columns:149px 1fr;margin-bottom:6px}
  .spec-col--right .spec-row{grid-template-columns:151px 1fr}
  .spec-row dt{font-weight:700;text-transform:uppercase;letter-spacing:.2px;padding-right:6px}
  .spec-row dd{font-weight:400}
  .company{left:347px;top:737px;white-space:nowrap}
  .company__name{color:var(--sky);font-weight:700;font-size:19px;letter-spacing:.6px}
  .company__cities{font-size:10px;font-weight:700;letter-spacing:.6px;margin-top:2px}
</style>
</head>
<body>

<section class="sheet sheet--front" aria-label="Brochure front">
  <svg class="backdrop-art" width="648" height="917" viewBox="0 0 648 917" aria-hidden="true">
    <polygon points="0,0 648,0 648,338 0,198" fill="var(--navy)"/>
    <polygon points="330,296 648,346 648,380 330,310" fill="var(--sky)"/>
    <polygon points="0,886 292,886 366,822 373,822 298,893 0,893" fill="var(--sky-soft)"/>
    <polygon points="300,893 376,822 648,822 648,893" fill="var(--navy)"/>
    <rect x="0" y="893" width="648" height="24" fill="var(--navy-deep)"/>
  </svg>

  <div class="product-photo" role="img" aria-label="Photo of the desk and floor-standing thermal scanning cameras"></div>

  <h1 class="title">
    <span class="title__thermal">THERMAL</span>
    <span class="title__scanning">SCANNING</span>
    <span class="title__sub">AND FACIAL RECOGNITION</span>
    <span class="title__camera">CAMERA</span>
  </h1>

  <div class="copy copy--left">
    <p>The temperature of your body is no longer considered private information. That's the stance that businesses around the world are taking as they install thermal imaging cameras for the safety of staff and visitors, often equipped with facial recognition technology, in their buildings in an attempt to cope with the COVID-19 pandemic. It's a movement one might call the automation of temperature checks.</p>
    <h3>THE PURPOSE OF THERMAL SCANNING &amp;<br>FACIAL RECOGNITION</h3>
    <p>The purpose is to identify anyone walking into an establishment with a high temperature. This will reduce the likelihood of spreading any potential virus and brings some peace of mind to people in the building.</p>
    <p>We can pair your thermal camera/s with facial recognition software. Employees will check in by standing in front of the camera, which identifies them by their face in just a few seconds without contact (with or without a mask on) and simulta­neously performs a thermal scan. It will record a photo of the individual, the date, the time and the temperature reading at that time of entering the building. If the camera detects a high temperature reading, it will sound an alarm in real time and send a notification to a nominated administrator/in-house security.</p>
  </div>

  <div class="copy copy--right">
    <h3>WHERE AND HOW CAN IT BE USED?</h3>
    <p>This Camera can be used with access control gates. It is used in office buildings, schools, hotels, hospitality, in fact, any space where Covid is potentially a threat to staff or visitors.</p>
    <p>Our Thermal Scanning &amp; Facial Recognition Camera is used as a safety and security measure.</p>
    <p>If someone gets sick and takes legal action, you can demonstrate that you have made your best effort to protect your staff and visitors.</p>
  </div>

  <div class="model-card model-card--desk">
    <span class="model-card__name">PORTABLE CAMERA FOR A RECEPTION DESK</span>
    <div class="model-card__photo" role="img" aria-label="Photo of the reception desk camera model"></div>
  </div>
  <div class="model-card model-card--floor">
    <span class="model-card__name">PORTABLE FLOOR STANDING CAMERA</span>
    <div class="model-card__photo" role="img" aria-label="Photo of the floor standing camera model"></div>
  </div>

  <div class="brand"><span class="brand__mark"></span>Korvel Display Group</div>

  <div class="contact">
    <div class="contact__phone">
      <svg width="18" height="18" viewBox="0 0 24 24" aria-hidden="true"><path fill="var(--sky-soft)" d="M6.6 10.8a15.1 15.1 0 0 0 6.6 6.6l2.2-2.2a1 1 0 0 1 1-.25 11.4 11.4 0 0 0 3.6.57 1 1 0 0 1 1 1V20a1 1 0 0 1-1 1A17 17 0 0 1 3 4a1 1 0 0 1 1-1h3.5a1 1 0 0 1 1 1c0 1.25.2 2.45.57 3.57a1 1 0 0 1-.25 1z"/></svg>
      1300 618 475
    </div>
    <div class="contact__note">for further information and a free quote</div>
    <div class="contact__web">
      <svg width="18" height="18" viewBox="0 0 24 24" aria-hidden="true" fill="none" stroke="var(--sky-soft)" stroke-width="2"><circle cx="12" cy="12" r="9"/><path d="M3 12h18M12 3c3 3.5 3 14.5 0 18M12 3c-3 3.5-3 14.5 0 18"/></svg>
      www.korveldisplay.com.au
    </div>
  </div>
</section>

<section class="sheet sheet--back" aria-label="Brochure back">
  <svg class="backdrop-art" width="648" height="917" viewBox="0 0 648 917" aria-hidden="true">
    <rect x="0" y="28" width="648" height="130" fill="var(--navy)"/>
    <rect x="0" y="162" width="648" height="4" fill="var(--sky)"/>
    <polygon points="0,886 292,886 366,822 373,822 298,893 0,893" fill="var(--sky-soft)"/>
    <polygon points="300,893 376,822 648,822 648,893" fill="var(--navy)"/>
    <rect x="0" y="893" width="648" height="24" fill="var(--navy-deep)"/>
  </svg>

  <h2 class="spec-title">TECHNICAL SPECIFICATIONS</h2>

  <div class="spec-col spec-col--left">
    <h4>CAMERA</h4>
    <dl>
      <div class="spec-row"><dt>Resolution:</dt><dd>2 million pixels</dd></div>
      <div class="spec-row"><dt>Type:</dt><dd>Binocular wide dynamic camera</dd></div>
      <div class="spec-row"><dt>Aperture:</dt><dd>F2.4</dd></div>
      <div class="spec-row"><dt>Focusing distance:</dt><dd>50-150cm</dd></div>
      <div class="spec-row"><dt>White balance:</dt><dd>Auto</dd></div>
      <div class="spec-row"><dt>Photo flood light:</dt><dd>LED and IR dual photo</dd></div>
      <div class="spec-row"><dt>Flood light</dt><dd></dd></div>
    </dl>
    <h4>SCREEN</h4>
    <dl>
      <div class="spec-row"><dt>Size:</dt><dd>8.0 inch IPS LCD screen</dd></div>
      <div class="spec-row"><dt>Resolution:</dt><dd>800x1280</dd></div>
      <div class="spec-row"><dt>Touch:</dt><dd>Not supported</dd></div>
    </dl>
    <h4>PROCESSOR</h4>
    <dl>
      <div class="spec-row"><dt>CPU:</dt><dd>KX3200 quad-core</dd></div>
      <div class="spec-row"><dt>Storage:</dt><dd>EMMC 8G</dd></div>
    </dl>
    <h4>INTERFACE</h4>
    <dl>
      <div class="spec-row"><dt>Interface:</dt><dd>Ethernet and wireless (WIFI)</dd></div>
      <div class="spec-row"><dt>Audio:</dt><dd>2.5W / 4R speakers</dd></div>
      <div class="spec-row"><dt>USB:</dt><dd>1 USB OTG, 1 USB HOST standard A port</dd></div>
      <div class="spec-row"><dt>Serial communication:</dt><dd>1 RS232 serial port</dd></div>
      <div class="spec-row"><dt>Relay output:</dt><dd>1 door open signal output</dd></div>
      <div class="spec-row"><dt>Wiegand one Wiegand:</dt><dd>26/34 output, one Wiegand 26/34 input</dd></div>
      <div class="spec-row"><dt>Upgrade button:</dt><dd>Support Uboot upgrade button</dd></div>
      <div class="spec-row"><dt>Wired network:</dt><dd>1 RJ45 Ethernet socket</dd></div>
    </dl>
    <h4>FUNCTION</h4>
    <dl>
      <div class="spec-row"><dt>Face detection:</dt><dd>Supports facial detection</dd></div>
      <div class="spec-row"><dt>Face library:</dt><dd>Up to 30,000</dd></div>
    </dl>
  </div>

  <div class="spec-col spec-col--right">
    <dl>
      <div class="spec-row"><dt>1: N face recognition:</dt><dd>Support</dd></div>
      <div class="spec-row"><dt>1: 1 face comparison:</dt><dd>Support</dd></div>
      <div class="spec-row"><dt>Stranger detection:</dt><dd>Support</dd></div>
      <div class="spec-row"><dt>Identify distance configuration:</dt><dd>Support</dd></div>
      <div class="spec-row"><dt>UI interface configuration:</dt><dd>Support</dd></div>
      <div class="spec-row"><dt>Upgrade remotely:</dt><dd>Support</dd></div>
      <div class="spec-row"><dt>Interface:</dt><dd>Interfaces include device management, personnel / photo management record query, etc.</dd></div>
      <div class="spec-row"><dt>Deployment method:</dt><dd>Support public cloud deployment, privatized deployment, LAN use stand-alone use</dd></div>
    </dl>
    <h4>INFRARED IMAGING THERMAL MODULE</h4>
    <dl>
      <div class="spec-row"><dt>Temperature detection:</dt><dd>Support</dd></div>
      <div class="spec-row"><dt>Temperature detection distance:</dt><dd>1 meter (optimal distance 0.5 meter)</dd></div>
      <div class="spec-row"><dt>Temperature:</dt><dd>≤ ±0.5° C measurement accuracy</dd></div>
      <div class="spec-row"><dt>Temperature measurement range:</dt><dd>10° C~42° C</dd></div>
      <div class="spec-row"><dt>Pixels:</dt><dd>32 X 32 dots (total 1024 pixels) Visitors' temperature is normal and released</dd></div>
      <div class="spec-row"><dt>Visitors' temperatur is normal and released directly:</dt><dd>Support</dd></div>
      <div class="spec-row"><dt>Abnormal temperature alarm:</dt><dd>Support (temperature alarm value can be set)</dd></div>
    </dl>
  </div>

  <div class="company">
    <div class="company__name">KORVEL DISPLAY GROUP</div>
    <div class="company__cities">MELBOURNE – SYDNEY – PERTH – BRISBANE</div>
  </div>

  <div class="brand"><span class="brand__mark"></span>Korvel Display Group</div>

  <div class="contact contact--short">
    <div class="contact__phone">
      <svg width="18" height="18" viewBox="0 0 24 24" aria-hidden="true"><path fill="var(--sky-soft)" d="M6.6 10.8a15.1 15.1 0 0 0 6.6 6.6l2.2-2.2a1 1 0 0 1 1-.25 11.4 11.4 0 0 0 3.6.57 1 1 0 0 1 1 1V20a1 1 0 0 1-1 1A17 17 0 0 1 3 4a1 1 0 0 1 1-1h3.5a1 1 0 0 1 1 1c0 1.25.2 2.45.57 3.57a1 1 0 0 1-.25 1z"/></svg>
      1300 618 475
    </div>
    <div class="contact__web">
      <svg width="18" height="18" viewBox="0 0 24 24" aria-hidden="true" fill="none" stroke="var(--sky-soft)" stroke-width="2"><circle cx="12" cy="12" r="9"/><path d="M3 12h18M12 3c3 3.5 3 14.5 0 18M12 3c-3 3.5-3 14.5 0 18"/></svg>
      www.korveldisplay.com.au
    </div>
  </div>
</section>

</body>
</html>
```